Maple Roster Business Card for recruitment company

We are looking for a Business Card Design that incorporates our personal details and our busines name and logo. We are a specialized search consultancy that recruit Property and Construction professionals.
We would like a business card that stands out and is appealing to the Construction and Property industry as well.

Target Market(s)

people in the construction and property industry

Contact Information for Business Card

Business Name and logo

Font styles to use
Serif

Colors
0094D4
00A9DD
6FCCEA
C7EBF8
E9F6FB

Requirements
Must have
• Business name and logo as well as contact details
Should not have
• No photos of us please

```html
<!DOCTYPE html>
<html lang="en">
<head>
<meta charset="utf-8">
<title>Maple Roster Business Card</title>
<link href="https://fonts.googleapis.com/css2?family=Lora:wght@400;700&display=swap" rel="stylesheet">
<style>
  :root {
    --backdrop: #2b2c2e;
    --brand-blue: #0094d4;
    --brand-blue-light: #00a9dd;
    --brand-sky: #6fccea;
    --brand-mist: #c7ebf8;
    --brand-ice: #e9f6fb;
    --card-white: #ffffff;
    --ink-dark: #2f3b45;
    --rule-grey: #c7ebf8;
  }
  * { box-sizing: border-box; margin: 0; padding: 0; }
  html, body { width: 1200px; height: 874px; overflow: hidden; }
  body {
    background: var(--backdrop);
    font-family: "Lora", serif;
    position: relative;
  }
  .card {
    position: absolute;
    left: 267px;
    width: 666px;
    height: 380px;
    border-radius: 22px;
    overflow: hidden;
  }
  .card-front {
    top: 36px;
    background: linear-gradient(135deg, var(--brand-blue-light), var(--brand-blue));
    display: flex;
    align-items: center;
    justify-content: center;
  }
  .brand-name {
    font-family: "Lora", serif;
    font-weight: 400;
    font-size: 52px;
    letter-spacing: 4px;
    color: var(--brand-ice);
  }
  .card-back {
    top: 458px;
    background: var(--card-white);
  }
  .holder {
    position: absolute;
    right: 340px;
    top: 118px;
    text-align: right;
  }
  .holder-name {
    font-weight: 700;
    font-size: 24px;
    color: var(--brand-blue);
    letter-spacing: 0.5px;
  }
  .holder-role {
    font-size: 15px;
    color: var(--ink-dark);
    margin-top: 2px;
  }
  .divider {
    position: absolute;
    left: 340px;
    top: 108px;
    width: 1px;
    height: 134px;
    background: var(--rule-grey);
  }
  .contact-list {
    position: absolute;
    left: 362px;
    top: 106px;
    list-style: none;
    font-size: 14px;
    color: var(--ink-dark);
    line-height: 21px;
  }
  .contact-list li {
    display: flex;
    align-items: flex-start;
    gap: 8px;
  }
  .contact-list svg {
    width: 13px;
    height: 13px;
    margin-top: 4px;
    flex: none;
    fill: var(--brand-blue);
  }
  .band {
    position: absolute;
    left: 0;
    right: 0;
    top: 268px;
    height: 66px;
    background: var(--brand-blue);
  }
  .band::before, .band::after {
    content: "";
    position: absolute;
    left: 0;
    right: 0;
    border-top: 1px dashed var(--brand-mist);
  }
  .band::before { top: 7px; }
  .band::after { bottom: 7px; }
  .web-address {
    position: absolute;
    left: 52px;
    top: 21px;
    font-size: 16px;
    letter-spacing: 4px;
    color: var(--card-white);
  }
  .brand-dot {
    position: absolute;
    right: 52px;
    top: 4px;
    width: 58px;
    height: 58px;
    border-radius: 50%;
    background: var(--brand-ice);
    border: 3px solid var(--brand-sky);
  }
</style>
</head>
<body>
  <section class="card card-front">
    <span class="brand-name">MAPLE ROSTER</span>
  </section>

  <section class="card card-back">
    <div class="holder">
      <p class="holder-name">DANIEL REYES</p>
      <p class="holder-role">President</p>
    </div>
    <div class="divider"></div>
    <ul class="contact-list">
      <li>
        <svg viewBox="0 0 12 12"><path d="M6 0a4 4 0 0 0-4 4c0 3 4 8 4 8s4-5 4-8a4 4 0 0 0-4-4zm0 5.6a1.6 1.6 0 1 1 0-3.2 1.6 1.6 0 0 1 0 3.2z"/></svg>
        <span>418 Birchwood Road<br>Juneau, Alaska 34520</span>
      </li>
      <li>
        <svg viewBox="0 0 12 12"><path d="M2.4 0.5l2 2.2-1 1.4c0.7 1.6 1.9 2.8 3.5 3.5l1.4-1 2.2 2-1.2 2.2C4.8 10.6 1.4 7.2 0.2 1.7z"/></svg>
        <span>555-218-4079</span>
      </li>
      <li>
        <svg viewBox="0 0 12 12"><path d="M3 0h6v12H3zM4 1.5v8h4v-8z"/></svg>
        <span>555-631-2904</span>
      </li>
      <li>
        <svg viewBox="0 0 12 12"><path d="M3 0h6v3H3zM1 4h10v5H9v3H3V9H1zm3 4v3h4V8z"/></svg>
        <span>555-407-1862</span>
      </li>
      <li>
        <svg viewBox="0 0 12 12"><path d="M0 2h12v1L6 7 0 3zM0 4.4l6 4 6-4V10H0z"/></svg>
        <span>daniel@mapleroster.com</span>
      </li>
    </ul>
    <div class="band">
      <span class="web-address">WWW.MAPLEROSTER.COM</span>
      <span class="brand-dot"></span>
    </div>
  </section>
</body>
</html>
```